New Business Card Design Project

We require a business card design for Vexalund, a newly established Indian company.
Our focus is on the development, manufacturing, and export of a diverse array of pharmaceutical products on a global scale. The card should convey a professional appearance, as our primary markets are in Africa, China, and Southeast Asian nations.
We envision a two-sided business card, with the reverse side dedicated to a logo set against a solid color or an elegantly designed pattern. The corners should be rounded. We would appreciate seeing both horizontal and vertical design options. We trust the designer to utilize their expertise in creating this design.

The content for the business card is included in the attached Word file.

Target Market(s)

Our primary markets are in Africa, China, and Southeast Asian, Latin America, Maldives, Sri Lanka

Industry/Entity Type

Pharmaceutical Manufacturing and Export

Contact Information for Business Card

Colors

Designer to choose colors to be used in the design.

Requirements
Must have
• The reverse side of the business card features solely the logo along with the tagline, "Wellness for All."
Should not have
• The logo should not exceed two instances, encompassing both the front and back sides of the card.

```html
<!DOCTYPE html>
<html lang="en">
<head>
<meta charset="utf-8">
<title>Vexalund Business Card</title>
<link rel="stylesheet" href="https://fonts.googleapis.com/css2?family=Montserrat:wght@700&family=Poppins:wght@300;400;500&display=swap">
<style>
  :root {
    --bg: #ece9e4;
    --navy-deep: #06324a;
    --blue-mid: #12618a;
    --blue-bright: #23a0d8;
    --brand-blue: #2199d3;
    --brand-red: #e2503a;
    --ink: #333a40;
    --white: #ffffff;
    --card-white: #f7f7f7;
  }
  * { box-sizing: border-box; margin: 0; padding: 0; }
  html, body { width: 1200px; height: 900px; overflow: hidden; }
  body {
    background: var(--bg);
    font-family: "Poppins", sans-serif;
    display: flex;
    flex-direction: column;
    align-items: center;
    justify-content: center;
    gap: 56px;
  }
  .card {
    width: 600px;
    height: 343px;
    border-radius: 34px;
    position: relative;
    overflow: hidden;
    box-shadow: 0 8px 22px rgba(0,0,0,0.18);
  }

  /* Back side */
  .card-back {
    background: radial-gradient(ellipse 60% 70% at 50% 62%, var(--blue-bright) 0%, var(--blue-mid) 50%, var(--navy-deep) 100%);
    color: var(--white);
    text-align: center;
  }
  .back-mark {
    position: absolute;
    left: 50%; top: 70px;
    transform: translateX(-50%);
    display: flex; flex-direction: column; align-items: center; gap: 14px;
  }
  .mark-dot {
    width: 38px; height: 38px; border-radius: 50%;
    background: var(--white);
  }
  .back-name {
    font-family: "Montserrat", sans-serif;
    font-weight: 700;
    font-size: 40px;
    letter-spacing: 1px;
  }
  .back-rule {
    position: absolute;
    left: 95px; right: 95px; top: 212px;
    height: 1px; background: rgba(255,255,255,0.8);
  }
  .tagline {
    position: absolute;
    left: 0; right: 0; top: 226px;
    font-weight: 400;
    font-size: 17px;
    letter-spacing: 7px;
  }

  /* Front side */
  .card-front {
    background: linear-gradient(120deg, #e9e9e9 0%, var(--card-white) 45%, var(--white) 100%);
    color: var(--ink);
  }
  .front-mark {
    position: absolute;
    left: 70px; top: 38px;
    display: flex; align-items: center; gap: 14px;
  }
  .front-mark .mark-dot { background: var(--brand-blue); width: 34px; height: 34px; }
  .front-name {
    font-family: "Montserrat", sans-serif;
    font-weight: 700;
    font-size: 52px;
    color: var(--brand-blue);
  }
  .person {
    position: absolute; left: 70px; top: 118px;
  }
  .person-name {
    font-weight: 500; font-size: 19px;
    color: var(--brand-red); letter-spacing: 0.3px;
  }
  .person-role {
    font-weight: 300; font-size: 15px; margin-top: 4px;
    display: flex; align-items: center; gap: 6px;
  }
  .person-role svg { width: 12px; height: 16px; }
  .address {
    position: absolute; right: 48px; top: 190px;
    text-align: right; font-style: normal; font-weight: 300; font-size: 15px; line-height: 1.45;
  }
  .front-rule {
    position: absolute; left: 40px; right: 40px; top: 250px;
    height: 1.5px; background: var(--brand-blue);
  }
  .contacts {
    position: absolute; left: 48px; top: 264px;
    list-style: none; font-weight: 300; font-size: 15px; line-height: 1.6;
  }
  .contacts li { display: flex; align-items: center; gap: 10px; }
  .contacts svg { width: 18px; height: 18px; }
</style>
</head>
<body>
  <section class="card card-back">
    <div class="back-mark">
      <span class="mark-dot"></span>
      <span class="back-name">Vexalund</span>
    </div>
    <div class="back-rule"></div>
    <p class="tagline">Wellness for All</p>
  </section>

  <section class="card card-front">
    <div class="front-mark">
      <span class="mark-dot"></span>
      <span class="front-name">Vexalund</span>
    </div>
    <div class="person">
      <p class="person-name">RAVINDRA K. SOLANKI</p>
      <p class="person-role">CEO Of Vexalund |
        <svg viewBox="0 0 12 16" aria-hidden="true"><rect x="1" y="0.8" width="10" height="14.4" rx="2" fill="none" stroke="#e2503a" stroke-width="1.4"/><circle cx="6" cy="12.6" r="0.9" fill="#e2503a"/></svg>
        +919876501234</p>
    </div>
    <address class="address">12, Sahyadri Colony<br>Nashik, 422005, India</address>
    <div class="front-rule"></div>
    <ul class="contacts">
      <li>
        <svg viewBox="0 0 18 18" aria-hidden="true"><g fill="none" stroke="#e2503a" stroke-width="1.2"><circle cx="9" cy="9" r="7.5"/><ellipse cx="9" cy="9" rx="3.4" ry="7.5"/><line x1="1.5" y1="9" x2="16.5" y2="9"/><line x1="2.8" y1="5" x2="15.2" y2="5"/><line x1="2.8" y1="13" x2="15.2" y2="13"/></g></svg>
        www.vexalund.com
      </li>
      <li>
        <svg viewBox="0 0 18 18" aria-hidden="true"><rect x="1" y="3.5" width="16" height="11" fill="#e2503a"/><polyline points="1,3.5 9,10 17,3.5" fill="none" stroke="#fff" stroke-width="1.3"/></svg>
        rsolanki@vexalund.com
      </li>
    </ul>
  </section>
</body>
</html>
```